Hip / Cool Business Card for Custom Accessory Company

I would like to get a 2 sided design for standard size business cards, glossy (2 inches x 3.5 inches). Can be landscape or portrait layout! The design should include our logo (attached). The card should be extremely clear that the company is Tidy Pebble. Should also have our URL clear. Should also use the color scheme seen on our upcoming site, tidypebble.example. The font we use is called "hurry up." Other than that, please go-to-town. We are targeting 15-45 y.o. market, with a skew on the 20-30 crowd. We do custom and stock iPhone cases as well as Cufflinks, Winestoppers; see the website for more.
Updates

Project Deadline Extended
Reason: Extending in case the US July 4th Holiday is keeping people from working!!

Industry/Entity Type

Landscape

Requirements
Must have
• Must be clear that the website is tidypebble.example. Must be clear that custom designs are an option.
Nice to have
• images of our designs. examples of our designs.
Should not have
• hard on the eyes contrasting colors such as orange on black. green on blue. Should not have any fonts that are considered "old" like Times New Roman. But decorative fonts are fine.

```html
<!DOCTYPE html>
<html lang="en">
<head>
<meta charset="utf-8">
<title>Tidy Pebble – Business Cards</title>
<link rel="stylesheet" href="https://fonts.googleapis.com/css2?family=Black+Ops+One&family=Cinzel:wght@400;700&family=Michroma&display=swap">
<style>
  :root {
    --page: #ececec;
    --card: #ffffff;
    --ink: #2b2b2b;
    --black: #111111;
    --red: #c4161c;
    --teal: #1d9aa3;
    --navy: #12306b;
    --grey: #555555;
  }
  * { margin: 0; padding: 0; box-sizing: border-box; }
  html, body { width: 1200px; height: 714px; overflow: hidden; background: var(--page); }
  .canvas { position: relative; width: 1200px; height: 714px; }

  .card {
    position: absolute;
    top: 202px;
    width: 540px;
    height: 309px;
    background: var(--card);
    box-shadow: 0 2px 10px rgba(0,0,0,0.15);
    overflow: hidden;
  }
  .card--info { left: 40px; }
  .card--brand { left: 620px; }

  /* Info side */
  .brand-mark {
    position: absolute;
    left: 58px; top: 70px;
    width: 78px; height: 78px;
    border-radius: 50%;
    background: var(--teal);
  }
  .brand-name {
    position: absolute;
    left: 150px; top: 88px;
    font-family: "Michroma", sans-serif;
    font-size: 29px;
    letter-spacing: 2px;
    color: var(--ink);
    white-space: nowrap;
  }
  .person { position: absolute; left: 58px; top: 180px; text-align: right; width: 180px; }
  .person__name { font-family: "Cinzel", serif; font-size: 17px; color: var(--red); }
  .person__role { font-family: "Cinzel", serif; font-size: 14px; color: var(--teal); }
  .divider {
    position: absolute;
    left: 252px; top: 160px;
    width: 1px; height: 82px;
    background: var(--red);
  }
  .contacts { position: absolute; left: 264px; top: 160px; list-style: none; }
  .contacts li {
    display: flex; align-items: center; gap: 6px;
    height: 19px;
    font-family: "Cinzel", serif;
    font-size: 11px;
    color: var(--grey);
    letter-spacing: 0.5px;
  }
  .contacts svg { width: 11px; height: 11px; flex: none; }
  .bands { position: absolute; left: 0; bottom: 0; width: 540px; height: 60px; }

  /* Brand side */
  .word {
    position: absolute;
    left: 0; width: 100%;
    text-align: center;
    font-family: "Black Ops One", sans-serif;
    color: var(--black);
    letter-spacing: 4px;
  }
  .word--top { top: 38px; font-size: 46px; }
  .word--bottom { top: 212px; font-size: 46px; }
  .brand-disc {
    position: absolute;
    left: 213px; top: 100px;
    width: 114px; height: 114px;
    border-radius: 50%;
    background: var(--teal);
  }
  .url {
    position: absolute;
    left: 0; width: 100%; top: 282px;
    text-align: center;
    font-family: "Cinzel", serif;
    font-size: 10px;
    letter-spacing: 5px;
    color: var(--grey);
  }
</style>
</head>
<body>
<main class="canvas">

  <section class="card card--info" aria-label="Card front">
    <div class="brand-mark" aria-hidden="true"></div>
    <div class="brand-name">TIDY PEBBLE</div>

    <div class="person">
      <p class="person__name">Owen Hartley</p>
      <p class="person__role">Consultant</p>
    </div>

    <div class="divider"></div>

    <ul class="contacts">
      <li>
        <svg viewBox="0 0 12 12"><circle cx="6" cy="6" r="6" fill="var(--red)"/><path d="M4 3.2l1.2 1.4-.7.8c.5 1 1.2 1.7 2.1 2.1l.8-.7L8.8 8 8 9c-2.6-.4-4.6-2.4-5-5z" fill="#fff"/></svg>
        07700 900 318
      </li>
      <li>
        <svg viewBox="0 0 12 12"><circle cx="6" cy="6" r="6" fill="var(--red)"/><rect x="4" y="3" width="4" height="6" rx="0.8" fill="#fff"/></svg>
        0117 496 0521
      </li>
      <li>
        <svg viewBox="0 0 12 12"><circle cx="6" cy="6" r="6" fill="var(--red)"/><rect x="3" y="4" width="6" height="4" fill="#fff"/><path d="M3 4l3 2.2L9 4" stroke="var(--red)" stroke-width="0.7" fill="none"/></svg>
        hello@tidypebble.example
      </li>
      <li>
        <svg viewBox="0 0 12 12"><circle cx="6" cy="6" r="6" fill="var(--red)"/><circle cx="6" cy="6" r="3" fill="none" stroke="#fff" stroke-width="0.8"/><path d="M3 6h6M6 3v6" stroke="#fff" stroke-width="0.6"/></svg>
        www.tidypebble.example
      </li>
    </ul>

    <svg class="bands" viewBox="0 0 540 60" preserveAspectRatio="none" aria-hidden="true">
      <defs>
        <linearGradient id="band-red" x1="0" x2="1" y1="0" y2="0">
          <stop offset="0" stop-color="#8e0f14"/>
          <stop offset="1" stop-color="var(--red)"/>
        </linearGradient>
        <linearGradient id="band-blue" x1="0" x2="1" y1="0" y2="0">
          <stop offset="0" stop-color="var(--navy)"/>
          <stop offset="0.5" stop-color="var(--teal)"/>
          <stop offset="1" stop-color="var(--navy)"/>
        </linearGradient>
      </defs>
      <polygon points="0,50 250,50 240,60 0,60" fill="url(#band-red)"/>
      <polygon points="262,60 540,10 540,22 284,60" fill="url(#band-blue)"/>
    </svg>
  </section>

  <section class="card card--brand" aria-label="Card back">
    <div class="word word--top">TIDY</div>
    <div class="brand-disc" aria-hidden="true"></div>
    <div class="word word--bottom">PEBBLE</div>
    <p class="url">WWW.TIDYPEBBLE.EXAMPLE</p>
  </section>

</main>
</body>
</html>
```